wealth management firm, professional group, new model

we have a logo that works but we need a card, white background using our colors...clean look

our tag line if can be used in

The Bridge From Client to Owner

```html
<!DOCTYPE html>
<html lang="en">
<head>
<meta charset="utf-8">
<title>Arven Wealth Partners – Business Card</title>
<link rel="stylesheet" href="https://fonts.googleapis.com/css2?family=Jost:wght@400;500;600&display=swap">
<style>
  :root {
    --navy: #14284f;
    --navy-deep: #0c1b3a;
    --navy-light: #1d3766;
    --paper: #ffffff;
    --paper-shade: #eeeeee;
    --rule: #b5b5b5;
    --ink: #1a2d55;
    --ink-soft: #3a4660;
    --backdrop: #e9e7e3;
  }
  * { margin: 0; padding: 0; box-sizing: border-box; }
  html, body {
    width: 1200px; height: 900px; overflow: hidden;
    background: var(--backdrop);
    font-family: "Jost", "Futura", sans-serif;
  }
  .canvas {
    position: relative; width: 1200px; height: 900px;
    display: flex; flex-direction: column; align-items: center;
    justify-content: center; gap: 40px;
  }
  .card {
    position: relative; width: 660px; height: 377px; overflow: hidden;
    box-shadow: 0 6px 18px rgba(0,0,0,.18);
  }

  /* Card back */
  .card-back .pattern {
    position: absolute; inset: 0;
    background: radial-gradient(ellipse at 50% 40%, var(--navy-light) 0%, var(--navy) 45%, var(--navy-deep) 100%);
  }
  .card-back .back-name {
    position: absolute; right: 70px; bottom: 110px;
    color: var(--paper); font-size: 15px; font-weight: 500;
    letter-spacing: .3em; text-transform: uppercase;
  }

  /* Card front */
  .card-front {
    background: linear-gradient(120deg, var(--paper-shade) 0%, var(--paper) 55%, var(--paper) 100%);
  }
  .brand {
    position: absolute; top: 62px; right: 60px; text-align: right;
    color: var(--ink); font-weight: 400; text-transform: uppercase;
    letter-spacing: .35em; line-height: 1.5;
  }
  .brand .brand-name { display: block; font-size: 34px; }
  .brand .brand-sub { display: block; font-size: 13px; letter-spacing: .22em; }

  .person {
    position: absolute; left: 48px; top: 234px; color: var(--ink);
  }
  .person .name-line { display: flex; align-items: baseline; gap: 10px; }
  .person .name { font-size: 19px; font-weight: 600; letter-spacing: .02em; text-transform: uppercase; }
  .person .divider { font-size: 20px; font-weight: 500; }
  .person .role { font-size: 15px; font-weight: 400; color: var(--ink-soft); }
  .person .phone { margin-top: 4px; font-size: 14px; color: var(--ink-soft); }

  .rule {
    position: absolute; left: 230px; right: 44px; top: 254px;
    height: 1px; background: var(--rule);
  }
  .contact-band {
    position: absolute; left: 0; right: 0; bottom: 0; height: 64px;
    background: var(--navy); color: var(--paper);
    display: flex; align-items: center; padding-left: 48px;
    font-size: 14.5px; letter-spacing: .02em;
  }
  .contact-band .sep { margin: 0 10px; }
</style>
</head>
<body>
  <main class="canvas">
    <section class="card card-back" aria-label="Card back">
      <div class="pattern" role="img" aria-label="Tonal repeating brand pattern on navy"></div>
      <span class="back-name">Arven</span>
    </section>

    <section class="card card-front" aria-label="Card front">
      <div class="brand">
        <span class="brand-name">Arven</span>
        <span class="brand-sub">Wealth Partners</span>
      </div>

      <div class="person">
        <div class="name-line">
          <span class="name">Daniel Reeve</span>
          <span class="divider">|</span>
          <span class="role">Director</span>
        </div>
        <p class="phone">P. 310-555-0142</p>
      </div>
      <div class="rule"></div>

      <footer class="contact-band">
        <span>E. info@arvenwealth.com</span><span class="sep">|</span>
        <span>www.arvenwealth.com</span><span class="sep">|</span>
        <span>12 Harbor Lane, Westfield 4021</span>
      </footer>
    </section>
  </main>
</body>
</html>
```